Food packaging label design

The product name Crisparelle, a thin, crispy, and delicious biscuit/cookie made from simple, all natural ingredients. Its name comes from the fact that it looks and tastes a lot like a biscotti cookie, but thinly sliced and much crispier and more delicious than a biscotti. There are currently two flavors: Pure Pecans, and Hazel Cherry.

I am looking for a fresh, eye catchy design to go on the label for a rice paper stand up pouch (pouch sample attached). Label size are as follows:

4 oz bag - Width X Height
top: 4.5" x 3.5" bottom: 4.5" x 1.5"

12 oz bag
top: 6.5" x 5.5" bottom: 6.5" x 1.5"

I would like for the top portion of the packaging to include:

Crisparelle name
Tag line " a thinner, crispier, and more delicious cousin to the biscotti"
simple and natural ingredients

bottom to include:
net weight
ingredients: wheat flour, eggs, sugar, almonds

Attached is a copy of something I created in powerpoint. you can recreate this using graphic designer software per label specs and improve on it or supprise me with something totally awesome. The key is that it that the colors and design needs to pop or contrast against the white rice paper bag and design needs to be eye catchy, fun and whimsical.

Please refer to link below for best practices for creating artwork for labels to ensure correct format for printing.
http://www.brightmarkprint.example/label-articles/best-practices-designing-custom-labels/

Good luck!
Updates

Target Market(s)

educated, health conscious consumers such as customers who shops at green basket, brewlane, market pauls

Industry/Entity Type

Graphic Designer

Requirements
Should not have
• busy or clutter design

```html
<!DOCTYPE html>
<html lang="en">
<head>
<meta charset="utf-8">
<title>Crisparelle Pouch Labels</title>
<link href="https://fonts.googleapis.com/css2?family=Archivo+Narrow:wght@400;700&family=Didact+Gothic&family=Great+Vibes&family=Oswald:wght@300;400&display=swap" rel="stylesheet">
<style>
:root{
  --paper:#ffffff;
  --cream:#f1eadf;
  --cream-light:#f6f1e9;
  --nut-band:#d8a066;
  --ink:#2a1c13;
  --ink-soft:#4b3a2f;
  --maroon:#7b2b1b;
  --rule:#3a2b22;
}
*{margin:0;padding:0;box-sizing:border-box}
html,body{width:1200px;height:456px;overflow:hidden;background:var(--paper)}
body{position:relative;font-family:"Didact Gothic",Arial,sans-serif;color:var(--ink)}

.panel{position:absolute;top:0;width:294px;height:456px;overflow:hidden}
.panel--front-a{left:0}
.panel--back-a{left:302px}
.panel--front-b{left:604px}
.panel--back-b{left:906px}

/* front label */
.front-top{position:absolute;left:0;top:0;width:100%;height:222px;background:var(--cream)}
.nut-band{position:absolute;left:0;top:0;width:100%;height:20px;background:linear-gradient(180deg,var(--nut-band),#e8c497)}
.brand-name{position:absolute;left:0;right:0;top:96px;text-align:center;font-family:"Archivo Narrow",Arial,sans-serif;font-weight:700;font-size:44px;letter-spacing:1px;color:var(--ink);text-transform:uppercase}
.flavor-row{position:absolute;left:18px;right:10px;top:184px;display:flex;align-items:center}
.flavor{width:76px;text-align:center;line-height:1}
.flavor__script{font-family:"Great Vibes",cursive;font-size:22px;color:var(--ink)}
.flavor__caps{font-family:"Oswald",Arial,sans-serif;font-size:11px;letter-spacing:.5px;text-transform:uppercase;color:var(--ink)}
.flavor-divider{width:1px;height:32px;background:var(--rule);margin:0 7px 0 4px}
.tagline{font-family:"Oswald",Arial,sans-serif;font-weight:400;font-size:11.5px;line-height:15px;text-transform:uppercase;color:var(--maroon)}
.tagline b{font-weight:400;color:var(--ink-soft)}
.front-bottom{position:absolute;left:0;top:350px;width:100%;height:106px;background:var(--cream)}
.slogan{position:absolute;left:0;right:0;top:22px;text-align:center;font-family:"Great Vibes",cursive;font-size:28px;color:var(--ink)}
.ingredients{position:absolute;left:10px;top:74px;font-family:"Oswald",Arial,sans-serif;font-weight:300;font-size:8.5px;text-transform:uppercase;color:var(--ink-soft)}
.ingredients strong{font-weight:400;color:var(--maroon)}
.net-wt{position:absolute;right:10px;bottom:8px;font-family:"Oswald",Arial,sans-serif;font-weight:300;font-size:7px;color:var(--ink)}

/* back label */
.panel--back{background:var(--cream)}
.story{position:absolute;left:8px;top:14px;width:145px;height:325px;overflow:hidden;background:var(--cream-light);border:1px solid var(--rule);padding:5px 7px;font-size:8.8px;line-height:14.6px;color:var(--ink)}
.nutrition{position:absolute;left:162px;top:14px;width:126px;height:279px;background:#fff;border:1px solid var(--rule);padding:3px 4px;font-family:"Archivo Narrow",Arial,sans-serif;font-size:5.4px;line-height:1.25;color:#000}
.nutrition__title{font-weight:700;font-size:15px;line-height:1;letter-spacing:-.2px}
.nutrition__serving{font-weight:700;font-size:7px;line-height:1.1;border-bottom:4px solid #000;padding-bottom:1px}
.nutrition .row{display:flex;justify-content:space-between;border-bottom:.6px solid #000;padding:1.5px 0}
.nutrition .row--thick{border-bottom:2.5px solid #000}
.nutrition .row--indent{padding-left:7px}
.nutrition .row b{font-weight:700}
.nutrition__note{padding:2px 0;font-size:4.6px;line-height:1.2}
.nutrition table{width:100%;border-collapse:collapse;font-size:4.4px;line-height:1.15}
.nutrition td{padding:0}
.nutrition td:nth-child(n+3){text-align:right}
.allergen{position:absolute;left:162px;width:126px;top:300px;text-align:center;font-size:9px;line-height:12px}
.allergen strong{font-family:"Archivo Narrow",Arial,sans-serif;font-weight:700;font-size:9.5px}
.maker{position:absolute;left:8px;width:145px;top:348px;text-align:center;font-size:10.5px;line-height:13px}
.maker strong{font-family:"Archivo Narrow",Arial,sans-serif;font-weight:700;font-size:12px}
.upc-box{position:absolute;left:162px;top:337px;width:126px;height:96px;border:1px solid var(--rule);display:flex;align-items:center;justify-content:center;text-align:center;font-family:"Archivo Narrow",Arial,sans-serif;font-weight:700;font-size:12px;line-height:16px}
.web{position:absolute;left:10px;top:418px;width:150px;font-family:"Archivo Narrow",Arial,sans-serif;line-height:1}
.web__label{font-size:5.6px;font-weight:700;text-transform:uppercase}
.web__url{font-size:12px;font-weight:700;text-transform:uppercase;margin-top:3px}
</style>
</head>
<body>

<!-- Hazel Cherry front -->
<section class="panel panel--front panel--front-a">
  <div class="front-top" role="img" aria-label="Soft scattered nut pattern background">
    <div class="nut-band" role="img" aria-label="Row of whole nuts along the top edge"></div>
  </div>
  <h1 class="brand-name">Crisparelle</h1>
  <div class="flavor-row">
    <div class="flavor"><div class="flavor__script">Hazel</div><div class="flavor__caps">Cherry</div></div>
    <div class="flavor-divider"></div>
    <p class="tagline">A thinner, <b>crispier, and more</b><br>delicious cousin to the biscotti</p>
  </div>
  <div class="front-bottom" role="img" aria-label="Soft scattered nut pattern background">
    <p class="slogan">Simple and Natural</p>
    <p class="ingredients"><strong>Ingredients:</strong> wheat flour, eggs, sugar, almonds, cranberry</p>
    <p class="net-wt">NET WT. 2 OZ.</p>
  </div>
</section>

<!-- Hazel Cherry back -->
<section class="panel panel--back panel--back-a">
  <p class="story">Crisparelle is a thin, crispy, and delicious biscuit/cookie made from simple, and all natural ingredients. Hazel flavour is made from just 4 simple ingredients: egg whites, all purpose flour, suger, and almonds. The name Crisparelle comes from its twice cooked process and then thinly sliced to perfection. The Crispy, nutty and delicious flavour resemble the of a biscotti, but without the guilt. In fact, except for naturally healthy fat from almonds. Crisparelle is made without any fat at all. it is an ideal snack for the health conscious snaker. Go ahead. Give it a try... There is a Good Chance you will be hooked!!!</p>
  <div class="nutrition">
    <div class="nutrition__title">Nutrition Facts</div>
    <div class="nutrition__serving">Serving Size (1 oz) (25g)<br>Serving Per Container 2</div>
    <div class="row">Amount per serving</div>
    <div class="row row--thick"><b>Calories 80</b><b>Calories from Fat 25</b></div>
    <div class="row" style="justify-content:flex-end">% Daily Value*</div>
    <div class="row"><b>Total Fat 2.5g</b><b>5%</b></div>
    <div class="row row--indent"><b>Saturated Fat 0g</b><b>0%</b></div>
    <div class="row row--indent"><b>Trans Fat 0g</b><span></span></div>
    <div class="row"><b>Cholesterol 0mg</b><b>0%</b></div>
    <div class="row"><b>Sodium 15mg</b><b>1%</b></div>
    <div class="row"><b>Total Carbohydrate 14g</b><b>5%</b></div>
    <div class="row row--indent"><b>Dietart Fiber1g</b><b>4%</b></div>
    <div class="row"><b>Sugars 8g 8g</b><span></span></div>
    <div class="row row--thick"><b>Proteins 3g</b><span></span></div>
    <div class="row"><b>Vitamin A 0%</b><b>• Vitamin C 0%</b></div>
    <div class="row row--thick"><b>Calcium 2%</b><b>• Iron 2%</b></div>
    <p class="nutrition__note">*Percent Daily Values are based on a 2,000 calorie diet Your daily values may be higher or lower depending on your calorie needs:</p>
    <table>
      <tr><td></td><td>Calories:</td><td>2,000</td><td>2,500</td></tr>
      <tr><td>Total Fat</td><td>Less then</td><td>65g</td><td>80g</td></tr>
      <tr><td>&nbsp;Saturated Fat</td><td>Less then</td><td>20g</td><td>25g</td></tr>
      <tr><td>Cholesterol</td><td>Less then</td><td>300mg</td><td>300mg</td></tr>
      <tr><td>Sodium</td><td>Less then</td><td>2,400mg</td><td>2,400mg</td></tr>
      <tr><td>Total Carbohydrate</td><td></td><td>300g</td><td>375g</td></tr>
      <tr><td>&nbsp;Dietry Fiber</td><td></td><td>25g</td><td>30g</td></tr>
    </table>
    <p class="nutrition__note">Calories per gram:<br>&nbsp;&nbsp;&nbsp;&nbsp;&nbsp;Fat 9 . Carbohydrate 4 . Protein 4</p>
  </div>
  <p class="allergen"><strong>CONTAINS:</strong><br>EGG, WHEAT, AND TREE NUT</p>
  <p class="maker"><strong>Made in the U.S.A</strong><br>Create and Distributed by Good Crumb Kitchen, LLC.<br>Maple Ridge, Georgia</p>
  <div class="upc-box">Reserved for<br>UPC Label</div>
  <div class="web"><div class="web__label">For orders and inquiries, please visit us at:</div><div class="web__url">www.crisparelle.example</div></div>
</section>

<!-- Pure Pecans front -->
<section class="panel panel--front panel--front-b">
  <div class="front-top" role="img" aria-label="Soft scattered nut pattern background">
    <div class="nut-band" role="img" aria-label="Row of whole nuts along the top edge"></div>
  </div>
  <h1 class="brand-name">Crisparelle</h1>
  <div class="flavor-row">
    <div class="flavor"><div class="flavor__caps">Pure</div><div class="flavor__script">Pecans</div></div>
    <div class="flavor-divider"></div>
    <p class="tagline">A thinner, <b>crispier, and more</b><br>delicious cousin to the biscotti</p>
  </div>
  <div class="front-bottom" role="img" aria-label="Soft scattered nut pattern background">
    <p class="slogan">Simple and Natural</p>
    <p class="ingredients"><strong>Ingredients:</strong> wheat flour, eggs, sugar, almonds</p>
    <p class="net-wt">NET WT. 2 OZ.</p>
  </div>
</section>

<!-- Pure Pecans back -->
<section class="panel panel--back panel--back-b">
  <p class="story">Crisparelle is a thin, crispy, and delicious biscuit/cookie made from simple, and all natural ingredients. Pecan flavour is made from just 4 simple ingredients: egg whites, all purpose flour, suger, and almonds. The name Crisparelle comes from its twice cooked process and then thinly sliced to perfection. The Crispy, nutty and delicious flavour resemble the of a biscotti, but without the guilt. In fact, except for naturally healthy fat from almonds. Crisparelle is made without any fat at all. it is an ideal snack for the health conscious snaker. Go ahead. Give it a try... There is a Good Chance you will be hooked!!!</p>
  <div class="nutrition">
    <div class="nutrition__title">Nutrition Facts</div>
    <div class="nutrition__serving">Serving Size (1 oz) (28g)<br>Serving Per Container 2</div>
    <div class="row">Amount per serving</div>
    <div class="row row--thick"><b>Calories 90</b><b>Calories from Fat 25</b></div>
    <div class="row" style="justify-content:flex-end">% Daily Value*</div>
    <div class="row"><b>Total Fat 3g</b><b>5%</b></div>
    <div class="row row--indent"><b>Saturated Fat 0g</b><b>0%</b></div>
    <div class="row row--indent"><b>Trans Fat 0g</b><span></span></div>
    <div class="row"><b>Cholesterol 0mg</b><b>0%</b></div>
    <div class="row"><b>Sodium 15mg</b><b>1%</b></div>
    <div class="row"><b>Total Carbohydrate 14g</b><b>5%</b></div>
    <div class="row row--indent"><b>Dietart Fiber1g</b><b>4%</b></div>
    <div class="row"><b>Sugars 8g 8g</b><span></span></div>
    <div class="row row--thick"><b>Proteins 3g</b><span></span></div>
    <div class="row"><b>Vitamin A 0%</b><b>• Vitamin C 0%</b></div>
    <div class="row row--thick"><b>Calcium 2%</b><b>• Iron 2%</b></div>
    <p class="nutrition__note">*Percent Daily Values are based on a 2,000 calorie diet Your daily values may be higher or lower depending on your calorie needs:</p>
    <table>
      <tr><td></td><td>Calories:</td><td>2,000</td><td>2,500</td></tr>
      <tr><td>Total Fat</td><td>Less then</td><td>65g</td><td>80g</td></tr>
      <tr><td>&nbsp;Saturated Fat</td><td>Less then</td><td>20g</td><td>25g</td></tr>
      <tr><td>Cholesterol</td><td>Less then</td><td>300mg</td><td>300mg</td></tr>
      <tr><td>Sodium</td><td>Less then</td><td>2,400mg</td><td>2,400mg</td></tr>
      <tr><td>Total Carbohydrate</td><td></td><td>300g</td><td>375g</td></tr>
      <tr><td>&nbsp;Dietry Fiber</td><td></td><td>25g</td><td>30g</td></tr>
    </table>
    <p class="nutrition__note">Calories per gram:<br>&nbsp;&nbsp;&nbsp;&nbsp;&nbsp;Fat 9 . Carbohydrate 4 . Protein 4</p>
  </div>
  <p class="allergen"><strong>CONTAINS:</strong><br>EGG, WHEAT, AND TREE NUT</p>
  <p class="maker"><strong>Made in the U.S.A</strong><br>Create and Distributed by Good Crumb Kitchen, LLC.<br>Maple Ridge, Georgia</p>
  <div class="upc-box">Reserved for<br>UPC Label</div>
  <div class="web"><div class="web__label">For orders and inquiries, please visit us at:</div><div class="web__url">www.crisparelle.example</div></div>
</section>

</body>
</html>
```